Electronic Letterhead for The Harborline Partners, LLC

I would like to have an electronic letterhead layout using Word for first and second page letterhead using my previously designed logo. The logo was successfully designed by a designer for the Pixel Bazaar. I would like to only use the "C" portion of the logo on the second page. I would like the designer that designed my logo to be included in the designers that participate in this competition.

Target Market(s)

My clients are typically governmental entities or financial entities

Industry/Entity Type

Electronic

Font styles to use
Sans Serif

Requirements
Must have
• Utilize existing logo
Nice to have
• Fist and second page letterhead design in electronic format (Word)

```html
<!DOCTYPE html>
<html lang="en">
<head>
<meta charset="utf-8">
<title>The Harborline Partners, LLC — Letterhead</title>
<link href="https://fonts.googleapis.com/css2?family=Questrial&display=swap" rel="stylesheet">
<style>
  :root {
    --backdrop: #e8e8e7;
    --paper: #f6f6f5;
    --brand-blue: #2c4e86;
    --brand-grey: #5f5f5f;
    --text-grey: #6b6b6b;
    --rule-grey: #c9c9c9;
    --watermark: #ececeb;
  }
  * { margin: 0; padding: 0; box-sizing: border-box; }
  html, body {
    width: 1200px; height: 815px; overflow: hidden;
    background: var(--backdrop);
    font-family: "Questrial", "Century Gothic", sans-serif;
  }
  .canvas { position: relative; width: 1200px; height: 815px; }

  .sheet {
    position: absolute; top: 70px; width: 484px; height: 685px;
    background: var(--paper); overflow: hidden;
  }
  .sheet--first { left: 80px; }
  .sheet--continuation { left: 638px; }

  .sheet__watermark {
    position: absolute; left: 240px; top: -100px;
    width: 290px; height: 290px; border-radius: 50%;
    background: var(--watermark);
  }

  .brand { position: absolute; left: 35px; top: 38px; display: flex; align-items: center; gap: 10px; }
  .brand__dot { width: 44px; height: 44px; border-radius: 50%; background: var(--brand-blue); }
  .brand__name { color: var(--brand-blue); line-height: 1.05; text-transform: uppercase; }
  .brand__name span { display: block; }
  .brand__small { font-size: 10px; }
  .brand__large { font-size: 15px; letter-spacing: 0.2px; }
  .brand__mid { font-size: 13px; }

  .mark-dot {
    position: absolute; left: 35px; top: 46px;
    width: 29px; height: 29px; border-radius: 50%; background: var(--brand-blue);
  }

  .footer {
    position: absolute; left: 33px; right: 34px; top: 640px;
    display: flex; align-items: center; font-size: 7px; color: var(--text-grey); line-height: 10px;
  }
  .footer__group { padding: 0 10px; border-left: 1px solid var(--rule-grey); }
  .footer__group:first-child { padding-left: 0; border-left: none; }
  .footer__line { display: flex; align-items: center; gap: 4px; }
  .footer__line svg { width: 7px; height: 7px; flex: none; }
  .footer__line strong { color: var(--brand-blue); font-weight: 400; }
  .footer__web b { font-weight: 400; color: var(--brand-blue); }
  .footer__signoff { margin-left: auto; text-align: right; font-size: 8px; line-height: 9px; text-transform: uppercase; }

  .band { position: absolute; bottom: 0; height: 14px; }
  .band--blue { left: 0; width: 356px; background: var(--brand-blue); }
  .band--grey { right: 0; width: 125px; background: var(--brand-grey); }
</style>
</head>
<body>
<div class="canvas">

  <section class="sheet sheet--first" aria-label="First page letterhead">
    <div class="sheet__watermark" aria-hidden="true"></div>

    <header class="brand">
      <div class="brand__dot" aria-hidden="true"></div>
      <div class="brand__name">
        <span class="brand__small">The</span>
        <span class="brand__large">Harborline</span>
        <span class="brand__mid">Partners, LLC</span>
      </div>
    </header>

    <footer class="footer">
      <div class="footer__group">
        <div>240 Keel Avenue</div>
        <div>Marlow, OH 43610</div>
      </div>
      <div class="footer__group">
        <div class="footer__line">
          <svg viewBox="0 0 10 10" aria-hidden="true"><circle cx="5" cy="5" r="4.4" fill="none" stroke="#5f5f5f" stroke-width="1"/><path d="M3.3 2.8c0 2.3 1.6 4 3.9 4.2l.2-1-1.1-.5-.5.5c-.8-.4-1.4-1-1.7-1.8l.5-.5-.5-1.1z" fill="#5f5f5f"/></svg>
          419-555-0142
        </div>
        <div class="footer__line">
          <svg viewBox="0 0 10 10" aria-hidden="true"><circle cx="5" cy="5" r="4.4" fill="none" stroke="#5f5f5f" stroke-width="1"/><rect x="2.8" y="3.5" width="4.4" height="3.2" fill="#5f5f5f"/></svg>
          866-555-0178
        </div>
      </div>
      <div class="footer__group">
        <div class="footer__line">
          <svg viewBox="0 0 10 10" aria-hidden="true"><circle cx="5" cy="5" r="4.4" fill="none" stroke="#5f5f5f" stroke-width="1"/><path d="M2.8 3.4h4.4v3.2H2.8zM2.8 3.4L5 5.2l2.2-1.8" fill="none" stroke="#5f5f5f" stroke-width=".8"/></svg>
          info@harborlinepartners.com
        </div>
        <div class="footer__line footer__web">
          <svg viewBox="0 0 10 10" aria-hidden="true"><circle cx="5" cy="5" r="4.4" fill="none" stroke="#5f5f5f" stroke-width="1"/><circle cx="5" cy="5" r="2.4" fill="none" stroke="#5f5f5f" stroke-width=".7"/><path d="M2.6 5h4.8M5 2.6v4.8" stroke="#5f5f5f" stroke-width=".6"/></svg>
          <span>www.<b>harborlinepartners</b>.com</span>
        </div>
      </div>
      <div class="footer__signoff">The Harborline<br>Partners, LLC</div>
    </footer>

    <div class="band band--blue"></div>
    <div class="band band--grey"></div>
  </section>

  <section class="sheet sheet--continuation" aria-label="Second page letterhead">
    <div class="mark-dot" aria-hidden="true"></div>
    <div class="band band--blue"></div>
    <div class="band band--grey"></div>
  </section>

</div>
</body>
</html>
```